Velvet Lantern rebranding my business with a new business card

I have my new logo and now I need a refresher on my business cards. I really want something fun and fresh. I like black background or anything to make the color pop.
Logo
Name: Velvet Lantern
Contact Info as stated below:
Mira Pellow
555-013-4762
Logo
Name: Velvet Lantern
Mira Pellow
555-013-4762
fb.me/VelvetLanternbyMira
Instagram: @VelvetLanternbyMira

Industry/Entity Type

Business

Contact Information for Business Card

double-sided. Logo on one side. Contact info on the other.

Requirements
Must have
• Logo
• Name: Velvet Lantern
• Contact Info as stated below:
• Mira Pellow
• 555-013-4762
• fb.me/VelvetLanternbyMira
• fb.me/VelvetLanternbyMira

```html
<!DOCTYPE html>
<html lang="en">
<head>
<meta charset="utf-8">
<title>Velvet Lantern business card</title>
<link href="https://fonts.googleapis.com/css2?family=Roboto+Condensed:wght@400;700&display=swap" rel="stylesheet">
<style>
  :root {
    --stage: #ece7e2;
    --card-white: #ffffff;
    --pink: #f0a3b6;
    --pink-light: #f5b8c7;
    --pink-ring: #f3a9bb;
    --ink: #1f1f1f;
    --ink-soft: #3a3a3a;
  }
  html, body {
    margin: 0;
    padding: 0;
    width: 1200px;
    height: 911px;
    overflow: hidden;
    background: var(--stage);
    font-family: "Roboto Condensed", Arial, sans-serif;
  }
  .canvas {
    position: relative;
    width: 1200px;
    height: 911px;
  }
  .card {
    position: absolute;
    width: 580px;
    height: 350px;
    border-radius: 26px;
    overflow: hidden;
    box-shadow: 0 6px 18px rgba(0,0,0,0.18);
  }
  /* Front: contact side */
  .card-front {
    left: 90px;
    top: 100px;
    background: var(--card-white);
  }
  .front-band {
    position: absolute;
    right: 0;
    top: 0;
    width: 170px;
    height: 100%;
    background: linear-gradient(180deg, var(--pink-light), var(--pink));
  }
  .logo-seal {
    position: absolute;
    width: 150px;
    height: 150px;
    border-radius: 50%;
    background: var(--card-white);
    border: 2px solid var(--pink-ring);
    box-shadow: 0 0 0 5px var(--card-white), 0 0 0 6px #8d8d8d;
    display: flex;
    align-items: center;
    justify-content: center;
    text-align: center;
  }
  .logo-seal .brand-name {
    font-family: "Roboto Condensed", Arial, sans-serif;
    font-weight: 700;
    font-size: 22px;
    line-height: 1.1;
    color: var(--ink);
    letter-spacing: 0.5px;
  }
  .card-front .logo-seal {
    left: 335px;
    top: 40px;
  }
  .contact-block {
    position: absolute;
    left: 38px;
    bottom: 36px;
    color: var(--ink);
  }
  .contact-name {
    margin: 0 0 10px;
    font-weight: 700;
    font-size: 26px;
    letter-spacing: -0.3px;
    text-transform: uppercase;
  }
  .contact-list {
    list-style: none;
    margin: 0;
    padding: 0;
    font-size: 17px;
    color: var(--ink-soft);
  }
  .contact-list li {
    display: flex;
    align-items: center;
    gap: 10px;
    margin: 3px 0;
  }
  .contact-list svg {
    width: 13px;
    height: 13px;
    flex: none;
  }
  /* Back: logo side */
  .card-back {
    left: 530px;
    top: 470px;
    background: var(--pink);
  }
  .card-back .logo-seal {
    left: 215px;
    top: 100px;
  }
  .back-url {
    position: absolute;
    left: 30px;
    top: 50%;
    transform: translate(-50%, -50%) rotate(90deg) translateY(-30px);
    transform-origin: center;
    font-size: 15px;
    letter-spacing: 7px;
    color: var(--ink);
    white-space: nowrap;
  }
</style>
</head>
<body>
<main class="canvas">

  <section class="card card-front" aria-label="Business card, contact side">
    <div class="front-band"></div>
    <div class="logo-seal">
      <span class="brand-name">Velvet<br>Lantern</span>
    </div>
    <div class="contact-block">
      <h1 class="contact-name">Mira Pellow</h1>
      <ul class="contact-list">
        <li>
          <svg viewBox="0 0 16 16" aria-hidden="true"><path fill="#1f1f1f" d="M3.6 1.2l2.3 2.6-1.3 1.9c.9 2 2.6 3.8 4.7 4.7l1.9-1.3 2.6 2.3-1.5 2.4C6.7 13.6 2.4 9.3 1.2 3z"/></svg>
          <span>555-013-4762</span>
        </li>
        <li>
          <svg viewBox="0 0 16 16" aria-hidden="true"><circle cx="8" cy="8" r="7" fill="none" stroke="#1f1f1f" stroke-width="1.6"/><path d="M1 8h14M8 1c-3 3.5-3 10.5 0 14M8 1c3 3.5 3 10.5 0 14" fill="none" stroke="#1f1f1f" stroke-width="1.2"/></svg>
          <span>www.velvetlantern.com</span>
        </li>
        <li>
          <svg viewBox="0 0 16 16" aria-hidden="true"><rect x="1" y="1" width="14" height="14" rx="2" fill="#1f1f1f"/></svg>
          <span>fb.me/VelvetLanternbyMira</span>
        </li>
      </ul>
    </div>
  </section>

  <section class="card card-back" aria-label="Business card, logo side">
    <div class="back-url">www.velvetlantern.com</div>
    <div class="logo-seal">
      <span class="brand-name">Velvet<br>Lantern</span>
    </div>
  </section>

</main>
</body>
</html>
```